Travel Agency Website - Simple General

Need a 7 page simple design that is pretty repetitive. Need to be able to load quickly that is SEO optimized. Trying to give ideas on what they can do, be personal as we are local, but at the same time come across as professional and get information easily with little burden.

- Landing Page
- Brimwell Vacations Page
- Family Trips
- Road Trips from Texas
- Other Destinations
- About Us Page
- Contact Us Page

Target Market(s)

Families

Coding

Coded - Design and coding required

Number of Pages Required

5+ page

Colors

Designer to choose colors to be used in the design.

Requirements
Must have
• Like it to flow easily with our logo. Use that for colors, etc.

```html
<!DOCTYPE html>
<html lang="en">
<head>
<meta charset="utf-8">
<title>Family Trips | Lanternway Travel Co.</title>
<link rel="stylesheet" href="https://fonts.googleapis.com/css2?family=Oswald:wght@500;600&family=Poppins:wght@400;500&display=swap">
<style>
:root{
  --teal:#0b4458;
  --teal-deep:#063a4d;
  --gold:#c4964a;
  --cream:#fcf7f1;
  --line:#c9d1d4;
  --white:#ffffff;
}
*{box-sizing:border-box;margin:0;padding:0}
html,body{width:865px;height:1200px;overflow:hidden}
body{position:relative;background:var(--cream);font-family:'Poppins',sans-serif;color:var(--teal)}
.abs{position:absolute}
.hero-bg{left:0;top:0;width:865px;height:185px;background:linear-gradient(180deg,rgba(214,190,150,.35),rgba(252,247,241,1)),linear-gradient(90deg,#e8dccb,#f1e3cc 40%,#eedbc0 70%,#e2d6c6)}
.brand{left:108px;top:8px;width:88px;height:74px;display:flex;align-items:center;gap:5px}
.brand-dot{width:12px;height:12px;border-radius:50%;background:var(--teal);flex:none}
.brand-name{font-family:'Oswald',sans-serif;font-weight:500;font-size:12px;line-height:1.1;color:var(--teal)}
.nav{left:295px;top:24px;width:462px;display:flex;justify-content:space-between;align-items:center;font-size:8px;font-weight:500;text-transform:uppercase}
.nav a{color:var(--teal);text-decoration:none;position:relative}
.nav a.active{color:var(--gold)}
.nav a.active::after{content:"";position:absolute;left:50%;bottom:-6px;width:21px;height:2px;margin-left:-10px;background:var(--gold);border-radius:2px}
.nav a.soft{color:#1e6f7c}
.page-title{left:0;width:865px;top:100px;text-align:center;font-family:'Oswald',sans-serif;font-weight:600;font-size:23px;letter-spacing:.2px}
.page-sub{left:0;width:865px;top:133px;text-align:center;font-size:8.5px}
.heading-flourish{left:585px;top:92px;width:90px;height:50px;border-radius:8px;background:linear-gradient(135deg,rgba(196,150,74,.10),rgba(11,68,88,.10))}
.trip{width:212px}
.trip-photo{height:149px}
.trip-tag{margin:9px 0 0 4px;font-family:'Oswald',sans-serif;font-weight:500;font-size:9.5px;color:var(--gold);line-height:1}
.trip-name{margin:3px 0 0 4px;font-family:'Oswald',sans-serif;font-weight:500;font-size:12px;line-height:1.1;text-transform:uppercase}
.family-photo{left:78px;top:620px;width:355px;height:440px;border-radius:140px 140px 0 0;background:linear-gradient(180deg,#d9b99a,#a9c1d8 45%,#3f6a9a 80%,#5b7fab)}
.plan-title{left:445px;width:259px;top:608px;text-align:center;font-family:'Oswald',sans-serif;font-weight:600;font-size:22px}
.field{left:445px;width:259px;height:29px;background:var(--white);border:1px solid var(--line);border-radius:4px;display:flex;align-items:center;justify-content:space-between;padding:0 12px 0 14px;font-family:'Oswald',sans-serif;font-weight:500;font-size:9px;text-transform:uppercase}
.field.date{font-family:'Poppins',sans-serif;font-weight:400;font-size:9.5px;padding-left:16px}
.field-label{left:445px;top:718px;font-family:'Oswald',sans-serif;font-weight:500;font-size:9px}
.notes{left:445px;top:835px;width:259px;height:88px;background:var(--white);border:1px solid var(--line);border-radius:4px;padding:10px 14px;font-size:9.5px}
.submit{left:445px;top:928px;width:259px;height:29px;background:var(--gold);border-radius:4px;color:var(--white);font-family:'Oswald',sans-serif;font-weight:500;font-size:9.5px;display:flex;align-items:center;justify-content:center}
.footer-brand{left:392px;top:1062px;width:80px;height:70px;display:flex;flex-direction:column;align-items:center;justify-content:center;gap:4px}
.footer-brand .brand-dot{background:var(--gold)}
.footer-brand .brand-name{color:var(--white);text-align:center}
.contact{left:108px;color:var(--white);font-size:8.5px;display:flex;align-items:center;gap:5px}
.contact-ico{width:13px;height:13px;border-radius:50%;background:var(--gold);display:flex;align-items:center;justify-content:center}
.social{top:1096px;width:22px;height:22px;border-radius:50%;background:var(--gold)}
.rule{left:108px;top:1168px;width:649px;height:1px;background:rgba(255,255,255,.18)}
.copy{left:0;width:865px;top:1179px;text-align:center;color:var(--white);font-size:7.5px}
.to-top{left:794px;top:1158px;width:20px;height:20px;border-radius:50%;background:#2a8f96;display:flex;align-items:center;justify-content:center}
</style>
</head>
<body>
<div class="abs hero-bg" role="img" aria-label="Faded collage of travellers and scenic destinations"></div>

<div class="abs brand"><span class="brand-dot"></span><span class="brand-name">Lanternway<br>Travel Co.</span></div>

<nav class="abs nav">
  <a href="#" aria-label="Home"><svg width="9" height="8" viewBox="0 0 10 9"><path d="M5 0 0 4.5h1.5V9h2.5V6h2v3h2.5V4.5H10z" fill="#0b4458"/></svg></a>
  <a href="#">Brimwell Vacations</a>
  <a href="#" class="active">Family Trips</a>
  <a href="#">Texas Road Trips</a>
  <a href="#">Other Destinations</a>
  <a href="#" class="soft">About Us</a>
  <a href="#">Contact Us</a>
</nav>

<div class="abs heading-flourish" role="img" aria-label="Decorative travel flourish beside the heading"></div>
<h1 class="abs page-title">FAMILY TRIPS WE'VE TAKEN TOGETHER</h1>
<p class="abs page-sub">Pictures of Trips Our Family Took</p>

<div class="abs trip" style="left:108px;top:169px"><div class="trip-photo" role="img" aria-label="Two travellers in red chairs before mountain ruins" style="background:linear-gradient(180deg,#8fc0d8,#5c6b5a 55%,#c9a25a)"></div><p class="trip-tag">TRIP A :</p><h2 class="trip-name">Alpine Escape</h2></div>
<div class="abs trip" style="left:326px;top:169px"><div class="trip-photo" role="img" aria-label="Crowded cobblestone market street" style="background:linear-gradient(180deg,#7fb0c8,#6a8a4c 40%,#a8755a 70%,#8a8c8c)"></div><p class="trip-tag">TRIP B :</p><h2 class="trip-name">Cobblestone Cities</h2></div>
<div class="abs trip" style="left:545px;top:169px"><div class="trip-photo" role="img" aria-label="Wooden cabin on a coastal cliff above the surf" style="background:linear-gradient(120deg,#b5793a,#6a5a3a 45%,#2f6f86 60%,#1e4f6a)"></div><p class="trip-tag">TRIP A :</p><h2 class="trip-name">Coastal Retreat</h2></div>

<div class="abs trip" style="left:108px;top:365px"><div class="trip-photo" role="img" aria-label="Hiker on red rocks above desert dunes at sunset" style="background:linear-gradient(160deg,#f0c070,#d98a3a 50%,#a8482a)"></div><p class="trip-tag">TRIP A :</p><h2 class="trip-name">Desert Wander</h2></div>
<div class="abs trip" style="left:326px;top:365px"><div class="trip-photo" role="img" aria-label="Hiker by a misty forest stream" style="background:linear-gradient(180deg,#9fc98a,#3f6a3a 50%,#4d6e6a 75%,#22342f)"></div><p class="trip-tag">TRIP B :</p><h2 class="trip-name">Forest Explorer</h2></div>
<div class="abs trip" style="left:545px;top:365px"><div class="trip-photo" role="img" aria-label="Two kayakers on a mountain lake" style="background:linear-gradient(180deg,#a9cde0,#5f7a86 35%,#2e5a46 55%,#2a6f92)"></div><p class="trip-tag">TRIP A :</p><h2 class="trip-name">Lake Side Adventure</h2></div>

<div class="abs family-photo" role="img" aria-label="Smiling family with a map pointing toward their next destination"></div>

<h2 class="abs plan-title">PLAN YOUR FAMILY TRIP</h2>
<div class="abs field" style="top:646px">Which trip are you interested in?<svg width="8" height="5" viewBox="0 0 8 5"><path d="M1 1l3 3 3-3" fill="none" stroke="#0b4458" stroke-width="1.3"/></svg></div>
<div class="abs field" style="top:681px">When would you like to go?<svg width="8" height="11" viewBox="0 0 8 11"><path d="M1 4l3-3 3 3M1 7l3 3 3-3" fill="none" stroke="#0b4458" stroke-width="1.2"/></svg></div>
<p class="abs field-label">WHEN WOULD YOU LIKE TO GO?</p>
<div class="abs field date" style="top:734px">MM/DD/YYYY<svg width="9" height="9" viewBox="0 0 9 9"><rect x=".5" y="1.5" width="8" height="7" fill="none" stroke="#0b4458" stroke-width=".8"/><path d="M.5 3.5h8M2 5h1M4 5h1M6 5h1M2 7h1M4 7h1M6 7h1" stroke="#0b4458" stroke-width=".8"/></svg></div>
<div class="abs field date" style="top:768px">MM/DD/YYYY<svg width="9" height="9" viewBox="0 0 9 9"><rect x=".5" y="1.5" width="8" height="7" fill="none" stroke="#0b4458" stroke-width=".8"/><path d="M.5 3.5h8M2 5h1M4 5h1M6 5h1M2 7h1M4 7h1M6 7h1" stroke="#0b4458" stroke-width=".8"/></svg></div>
<div class="abs field" style="top:801px;padding-left:12px">What kind of trip are you looking for?<svg width="8" height="5" viewBox="0 0 8 5"><path d="M1 1l3 3 3-3" fill="none" stroke="#0b4458" stroke-width="1.3"/></svg></div>
<div class="abs notes">Any Additional Notes?</div>
<div class="abs submit">SUBMIT REQUEST</div>

<svg class="abs" style="left:0;top:990px" width="865" height="210" viewBox="0 990 865 210">
  <path d="M0 1075 C250 1030 370 1040 432 1000 C494 1040 615 1030 865 1075 L865 1200 L0 1200Z" fill="#063a4d"/>
  <path d="M0 1082 C250 1042 370 1050 432 1010 C494 1050 615 1042 865 1082" fill="none" stroke="#ffffff" stroke-width="2"/>
  <path d="M0 1068 C250 1025 370 1032 432 993 C494 1032 615 1025 865 1068" fill="none" stroke="#2a8f96" stroke-width="1"/>
</svg>

<div class="abs footer-brand"><span class="brand-dot"></span><span class="brand-name">Lanternway<br>Travel Co.</span></div>

<div class="abs contact" style="top:1096px"><span class="contact-ico"><svg width="7" height="7" viewBox="0 0 10 10"><path d="M2 0l2 2.5-1 1.5c.8 1.5 1.5 2.2 3 3l1.5-1L10 8 8.5 10C4 9.5.5 6 0 1.5z" fill="#fff"/></svg></span>555.014.2290</div>
<div class="abs contact" style="top:1110px"><span class="contact-ico"><svg width="7" height="6" viewBox="0 0 10 8"><rect width="10" height="8" rx="1" fill="#fff"/><path d="M0 1l5 3.5L10 1" fill="none" stroke="#c4964a"/></svg></span>hello@lanternwaytravel.com</div>

<a class="abs social" style="left:710px" href="#" aria-label="Social profile one"></a>
<a class="abs social" style="left:734px" href="#" aria-label="Social profile two"></a>

<div class="abs rule"></div>
<p class="abs copy">© 2026 LanternwayTravel / All Rights Reserved</p>
<a class="abs to-top" href="#" aria-label="Back to top"><svg width="6" height="4" viewBox="0 0 6 4"><path d="M1 3l2-2 2 2" fill="none" stroke="#fff" stroke-width="1"/></svg></a>
</body>
</html>
```